Rig up a website for a Rigging Company

We already have a logo. Looking for a website design that works on pavlune.com.
Our rigging company uses semi trucks, forklifts, and similar equipment to move large machines.
Our logo is white, black and red.

Target Market(s)

Medical Industry (moving medical equipment), Utility Industry (power equipment), Food Industry (moving bottling/packing equipment), US Government (large equipment)

Industry/Entity Type

It Company

Coding

Coded - Design and coding required

Number of Pages Required

5+ page

Font styles to use
Sans Serif

Colors
ec1f27
ffffff
0355a3

Requirements
Must have
• Home page, About page, Services Page, and Contact Information page
Nice to have
• Pictures of semi and forklifts and ability to insert our own pictures of our equipment

```html
<!DOCTYPE html>
<html lang="en">
<head>
<meta charset="utf-8">
<title>Harlow Rigging – Home</title>
<link href="https://fonts.googleapis.com/css2?family=Open+Sans:wght@400;600;700&family=Roboto+Condensed:ital,wght@0,700;1,700&display=swap" rel="stylesheet">
<style>
:root{
  --red:#ec1f27;
  --blue:#0355a3;
  --black:#111111;
  --dark:#1c1c1c;
  --grey:#f1f1f1;
  --line:#d9d9d9;
  --text:#5a5a5a;
  --white:#ffffff;
}
*{box-sizing:border-box;margin:0;padding:0}
html,body{width:1200px;height:3228px;overflow:hidden}
body{font-family:"Open Sans",Arial,sans-serif;color:var(--text);background:var(--white);font-size:14px;line-height:1.6}
.head{font-family:"Roboto Condensed","Arial Narrow",sans-serif;font-weight:700;text-transform:uppercase}
.btn{display:inline-block;background:var(--red);color:var(--white);font-family:"Roboto Condensed",sans-serif;font-weight:700;font-size:14px;text-transform:uppercase;padding:10px 24px;letter-spacing:.5px}
.photo{display:block}

/* header */
.topbar{height:128px;display:flex;align-items:center;justify-content:space-between;padding:0 80px}
.brand{display:flex;align-items:center;gap:12px;font-family:"Roboto Condensed",sans-serif;font-weight:700;font-size:40px;color:var(--black);letter-spacing:.5px}
.brand-square{width:22px;height:22px;background:var(--red)}
.phone{display:flex;align-items:center;gap:14px;color:var(--red);font-weight:700;font-size:28px}
.phone-icon{width:40px;height:40px;border:2px solid var(--red);border-radius:50%;display:flex;align-items:center;justify-content:center}
.nav{height:40px;background:var(--black);display:flex;justify-content:space-between;padding:0 80px}
.nav a{color:var(--white);text-decoration:none;font-family:"Roboto Condensed",sans-serif;font-weight:700;font-size:14px;line-height:40px;padding:0 22px}
.nav a.active{background:var(--red)}

/* hero */
.hero{position:relative;height:508px}
.hero-bg{position:absolute;inset:0;background:linear-gradient(160deg,#5c8fc4 0%,#9fc2e2 45%,#dbe7f1 75%,#8d9aa6 100%)}
.hero-copy{position:absolute;left:80px;top:150px}
.hero-title{font-size:64px;font-style:italic;color:var(--white);line-height:1.05}
.hero-sub{font-size:36px;color:var(--red);font-weight:600;line-height:1.15;margin:14px 0 26px;max-width:560px}
.dots{position:absolute;left:76px;bottom:108px;display:flex;gap:12px}
.dots span{width:12px;height:12px;border-radius:50%;background:var(--white);opacity:.6}
.dots span.on{opacity:1;background:var(--red)}

/* welcome */
.welcome{height:520px;display:flex;padding:50px 72px 0;gap:40px}
.welcome-text{width:300px}
.section-title{font-size:34px;color:var(--black);line-height:1.1;margin-bottom:22px}
.welcome-text p{font-size:14px;margin-bottom:26px}
.welcome-photo{width:320px;height:420px;background:linear-gradient(180deg,#c9ccd1 0%,#a8aeb6 50%,#d46a3a 75%,#7c7f84 100%)}
.quick{width:360px;height:420px;background:var(--grey);padding:22px 22px}
.quick h3{font-size:34px;color:var(--black);font-style:italic;margin-bottom:12px}
.field{height:38px;background:var(--white);border:1px solid var(--line);margin-bottom:10px;padding:0 12px;line-height:38px;font-size:12px;color:#999;display:flex;justify-content:space-between}
.field.msg{height:100px}
.quick .btn{float:right;margin-top:6px}

/* services */
.services{height:404px;display:flex}
.services-photo{width:560px;background:linear-gradient(150deg,#2f6fb3 0%,#6ea3d6 50%,#c9d6e2 80%,#e6b23a 100%)}
.services-copy{flex:1;background:var(--black);padding:120px 80px 0 60px}
.services-copy h2{font-size:36px;color:var(--white);font-style:italic;margin-bottom:14px}
.services-copy p{color:#bbb;margin-bottom:26px}

/* equipment cards */
.cards{height:400px;display:flex;justify-content:space-between;padding:20px 72px 0}
.card{width:328px;height:340px;position:relative}
.card-photo{height:100%}
.card-label{position:absolute;left:0;right:0;bottom:0;height:58px;background:var(--red);color:var(--white);font-size:30px;font-style:italic;text-align:center;line-height:58px}

/* blog + testimonials */
.news{height:520px;display:flex;padding:40px 72px 0;gap:40px}
.blog{width:688px}
.col-title{font-size:34px;color:var(--black);border-bottom:1px solid var(--line);padding-bottom:8px;margin-bottom:24px}
.post{display:flex;gap:24px;margin-bottom:34px}
.post-photo{width:240px;height:140px;flex:none}
.post h4{color:var(--red);font-size:18px;line-height:1.2}
.date{font-size:11px;color:#888;margin:4px 0}
.post p{font-size:13px}
.more{font-family:"Roboto Condensed",sans-serif;font-weight:700;font-size:13px;color:var(--black);text-transform:uppercase;margin-top:8px;display:block}
.testimonials{width:328px}
.quote{background:var(--grey);padding:16px 18px;font-size:13px;margin-bottom:10px}
.author{display:flex;justify-content:space-between;align-items:center;margin-bottom:26px}
.author span{color:var(--red);font-family:"Roboto Condensed",sans-serif;font-weight:700;font-size:13px;text-transform:uppercase}
.avatar{width:60px;height:60px;border-radius:50%;background:linear-gradient(180deg,#9aa3ad,#4e5863)}

/* contact */
.contact{position:relative;height:380px}
.map{position:absolute;inset:0;background:linear-gradient(120deg,#dfe3d6 0%,#cfd8c4 40%,#e8e6df 70%,#d4dbcf 100%)}
.contact-box{position:absolute;left:400px;top:50px;width:400px;height:280px;background:var(--white);text-align:center;padding-top:30px}
.contact-box h2{color:var(--red);font-size:36px;font-style:italic}
.contact-box h3{color:var(--red);font-size:20px;margin:6px 0 12px}
.contact-line{display:flex;align-items:center;justify-content:center;gap:10px;font-size:14px;margin-bottom:8px;color:var(--black)}

/* footer */
.footer{height:280px;background:var(--grey);display:flex;padding:40px 72px 0;gap:60px}
.footer-about{width:300px}
.footer-about .brand{font-size:34px;margin-bottom:12px}
.footer-col h5{color:var(--red);font-family:"Roboto Condensed",sans-serif;font-size:15px;margin-bottom:10px}
.footer-col ul{list-style:none;font-size:13px;line-height:1.9}
.links{display:flex;gap:40px}
.signup{width:260px}
.signup p{font-size:13px;margin-bottom:12px}
.signup .field{margin-bottom:12px}
.signup .btn{float:right}
.bottom{height:48px;background:#e4e4e4;display:flex;align-items:center;justify-content:space-between;padding:0 72px;font-size:12px}
.social{display:flex;gap:14px}
.social span{width:18px;height:18px;background:#777;border-radius:3px}
</style>
</head>
<body>

<header class="topbar">
  <div class="brand"><span class="brand-square"></span>Harlow Rigging</div>
  <div class="phone">
    <span class="phone-icon"><svg width="20" height="20" viewBox="0 0 24 24"><path fill="#ec1f27" d="M6.6 10.8a15.1 15.1 0 0 0 6.6 6.6l2.2-2.2c.3-.3.7-.4 1-.2 1.1.4 2.3.6 3.6.6.6 0 1 .4 1 1V20c0 .6-.4 1-1 1A17 17 0 0 1 3 4c0-.6.4-1 1-1h3.5c.6 0 1 .4 1 1 0 1.3.2 2.5.6 3.6.1.3 0 .7-.2 1z"/></svg></span>
    1-800-555-0142
  </div>
</header>

<nav class="nav">
  <a class="active">HOME</a><a>ABOUT US</a><a>SERVICES</a><a>BLOG</a><a>GALLERY</a><a>CAREERS</a><a>LATEST NEWS</a><a>TESTIMONIALS</a><a>CONTACT US</a>
</nav>

<section class="hero">
  <div class="hero-bg photo" role="img" aria-label="Crane hook lifting a load against a blue sky"></div>
  <div class="hero-copy">
    <h1 class="head hero-title">Harlow Rigging Services</h1>
    <p class="hero-sub">We are in rigging service to move large machines..</p>
    <span class="btn">Read More</span>
  </div>
  <div class="dots"><span class="on"></span><span></span><span></span><span></span></div>
</section>

<section class="welcome">
  <div class="welcome-text">
    <h2 class="head section-title">Welcome to<br>Harlow Rigging</h2>
    <p>Our crews plan every move with care, from the first site walk to the final set. We measure doors, floors and loads, then pick the right truck, forklift or crane. Teams work in hospitals, plants and public sites, and each machine arrives safe, level and ready to run in its new home.</p>
    <span class="btn">Read More</span>
  </div>
  <div class="welcome-photo photo" role="img" aria-label="Forklift in a warehouse"></div>
  <form class="quick">
    <h3 class="head">Quick Contact</h3>
    <div class="field">Name</div>
    <div class="field">Email Address</div>
    <div class="field">Phone No</div>
    <div class="field">Select Service <span>▾</span></div>
    <div class="field msg">Message</div>
    <span class="btn">Submit</span>
  </form>
</section>

<section class="services">
  <div class="services-photo photo" role="img" aria-label="Crane lifting a large crate under a bright sky"></div>
  <div class="services-copy">
    <h2 class="head">Our Services</h2>
    <p>We move heavy machines for medical, utility, food and government clients. Each job gets a written lift plan, trained riggers and equipment sized for the load, so your line is back in service on schedule.</p>
    <span class="btn">Read More</span>
  </div>
</section>

<section class="cards">
  <div class="card">
    <div class="card-photo photo" role="img" aria-label="White semi truck" style="background:linear-gradient(180deg,#dfe6ee,#b5bcc4 60%,#6f757b)"></div>
    <div class="card-label head">Semi Trucks</div>
  </div>
  <div class="card">
    <div class="card-photo photo" role="img" aria-label="Yellow forklift in a warehouse" style="background:linear-gradient(180deg,#bfc4c9,#d8b347 55%,#5f6368)"></div>
    <div class="card-label head">Forklifts</div>
  </div>
  <div class="card">
    <div class="card-photo photo" role="img" aria-label="Rigging shackles and chains" style="background:linear-gradient(180deg,#e4e4e4,#9ca1a6 55%,#4d5156)"></div>
    <div class="card-label head">Equipments</div>
  </div>
</section>

<section class="news">
  <div class="blog">
    <h2 class="head col-title">Blog Posts</h2>
    <article class="post">
      <div class="post-photo photo" role="img" aria-label="Crane hook over a job site" style="background:linear-gradient(160deg,#7fa9d2,#c7d8e6 60%,#d99a3b)"></div>
      <div>
        <h4 class="head">Aliquam molestie imperdiet euismod</h4>
        <div class="date">MAR 23, 2017</div>
        <p>A look at how our crew moved a full bottling line across town in two days without a single scratch.</p>
        <span class="more">Read More</span>
      </div>
    </article>
    <article class="post">
      <div class="post-photo photo" role="img" aria-label="Steel shackles and rigging hardware" style="background:linear-gradient(160deg,#9a8b73,#c6b79a 50%,#5e5446)"></div>
      <div>
        <h4 class="head">Aliquam molestie imperdiet euismod</h4>
        <div class="date">MAR 23, 2017</div>
        <p>Planning a hospital move starts months ahead. Here is how we protect imaging gear on the way in.</p>
        <span class="more">Read More</span>
      </div>
    </article>
  </div>
  <aside class="testimonials">
    <h2 class="head col-title">Testimonials</h2>
    <blockquote class="quote">The team moved our press line over one weekend and had it running by Monday. Clear plan, no surprises.</blockquote>
    <div class="author"><span>Dana Whitlock</span><div class="avatar photo" role="img" aria-label="Client portrait"></div></div>
    <blockquote class="quote">Careful, quick and always on time. They handled our generator swap with real skill and good humor.</blockquote>
    <div class="author"><span>Marcus Reyes</span><div class="avatar photo" role="img" aria-label="Client portrait"></div></div>
  </aside>
</section>

<section class="contact">
  <div class="map photo" role="img" aria-label="Map of the office location"></div>
  <div class="contact-box">
    <h2 class="head">Contact Us</h2>
    <h3 class="head">Harlow Rigging</h3>
    <div class="contact-line"><svg width="14" height="16" viewBox="0 0 24 28"><path fill="#ec1f27" d="M12 0a9 9 0 0 0-9 9c0 7 9 19 9 19s9-12 9-19a9 9 0 0 0-9-9zm0 12a3 3 0 1 1 0-6 3 3 0 0 1 0 6z"/></svg>4120 Quarry Lane, Salem, USA 97301</div>
    <div class="contact-line"><svg width="14" height="14" viewBox="0 0 24 24"><path fill="#ec1f27" d="M6.6 10.8a15.1 15.1 0 0 0 6.6 6.6l2.2-2.2c.3-.3.7-.4 1-.2 1.1.4 2.3.6 3.6.6.6 0 1 .4 1 1V20c0 .6-.4 1-1 1A17 17 0 0 1 3 4c0-.6.4-1 1-1h3.5c.6 0 1 .4 1 1 0 1.3.2 2.5.6 3.6.1.3 0 .7-.2 1z"/></svg>1-800-555-0142</div>
    <div class="contact-line"><svg width="16" height="12" viewBox="0 0 24 18"><rect x="1" y="1" width="22" height="16" fill="none" stroke="#ec1f27" stroke-width="2"/><path d="M1 1l11 9 11-9" fill="none" stroke="#ec1f27" stroke-width="2"/></svg>info@pavlune.com</div>
  </div>
</section>

<footer class="footer">
  <div class="footer-about">
    <div class="brand"><span class="brand-square"></span>Harlow Rigging</div>
    <p>Licensed and insured riggers serving industry and government for over twenty years.</p>
  </div>
  <div class="footer-col">
    <h5>SITE MAP</h5>
    <div class="links">
      <ul><li>Home</li><li>About Us</li><li>Services</li><li>Blog</li><li>Gallery</li><li>Careers</li></ul>
      <ul><li>Latest News</li><li>Testimonials</li><li>Contact Us</li></ul>
    </div>
  </div>
  <div class="footer-col">
    <h5>SERVICES</h5>
    <ul><li>Machine moving</li><li>Crane service</li><li>Millwright work</li><li>Storage</li></ul>
  </div>
  <div class="footer-col signup">
    <h5>SIGN UP EMAIL</h5>
    <p>Get news and offers in your inbox.</p>
    <div class="field">Enter Email Address</div>
    <span class="btn">Sign Up</span>
  </div>
</footer>
<div class="bottom">
  <span>Copyright © 2017 Harlow Rigging. All Rights Reserved.</span>
  <div class="social" aria-label="Social links"><span></span><span></span><span></span><span></span><span></span></div>
</div>

</body>
</html>
```